Willowmere Commons Shopping Center Brochure

Take the three attached files, request any additional information that may be needed and produce an attractive and effective pdf marketing brochure that will help make our shopping center lease up.  Would prefer most, if not all, of the text in the word file to be included.  Other than that parameter we are looking for a winning look.  The attached pdf file has too much information and ONLY page one should be used.  We would like all the tables and accompanying text in the Excel workbook to be used.
Thank you!

Target Market(s)
Entrepreneurs who need a commercial retail space to operate their businesses from.
Industry/Entity Type
Marketing
Look and feel

```html
<!DOCTYPE html>
<html lang="en">
<head>
<meta charset="utf-8">
<title>Willowmere Commons Shopping Center – Brochure Pages</title>
<link rel="stylesheet" href="https://fonts.googleapis.com/css2?family=Inter:wght@200;400&display=swap">
<style>
  :root {
    --canvas-bg: #d9d9d9;
    --panel-top: #eef0f9;
    --panel-bottom: #d5daf0;
    --band-light: #3f5fb8;
    --band-dark: #1e3378;
    --ink: #141414;
    --cover-center: #2f4f9e;
    --cover-edge: #1f3370;
    --sky: #c9d3dc;
    --ground: #b9ad98;
    --white: #ffffff;
    --mark: #e9c21a;
  }
  * { margin: 0; padding: 0; box-sizing: border-box; }
  html, body { width: 1200px; height: 860px; overflow: hidden; }
  body {
    background: var(--canvas-bg);
    font-family: "Inter", Arial, sans-serif;
    position: relative;
  }
  .page {
    position: absolute;
    width: 497px;
    height: 746px;
  }
  .page--inside { left: 65px; top: 54px; background: var(--white); }
  .page--back {
    left: 641px; top: 57px;
    background: radial-gradient(ellipse 70% 55% at 50% 40%, var(--cover-center), var(--cover-edge));
  }
  .intro {
    height: 258px;
    background: linear-gradient(180deg, var(--panel-top), var(--panel-bottom));
    padding: 38px 40px 0 42px;
    color: var(--ink);
  }
  .intro__title {
    font-weight: 200;
    font-size: 53px;
    letter-spacing: -1px;
    line-height: 1;
  }
  .intro__text {
    margin-top: 26px;
    font-size: 19px;
    line-height: 28px;
    font-weight: 400;
  }
  .band {
    height: 15px;
    background: linear-gradient(90deg, var(--band-dark), var(--band-light) 50%, var(--band-dark));
  }
  .photo {
    background: linear-gradient(180deg, var(--sky) 0%, #dfe5ea 55%, #a9a08c 78%, var(--ground) 100%);
  }
  .photo--sign { height: 285px; }
  .photo--wide { height: 173px; }
  .contact {
    position: absolute;
    left: 0; right: 0; top: 598px;
    text-align: center;
    color: var(--white);
  }
  .contact__brand {
    display: inline-flex;
    align-items: center;
    gap: 6px;
    font-size: 13px;
    font-weight: 400;
    letter-spacing: 0.5px;
    margin-bottom: 16px;
  }
  .contact__square { width: 12px; height: 12px; background: var(--mark); }
  .contact__line { font-size: 11px; line-height: 14px; }
</style>
</head>
<body>
  <section class="page page--inside">
    <div class="intro">
      <h1 class="intro__title">Excellent Signage</h1>
      <p class="intro__text">A large pole sign is on Marrow Creek road with each tenant entrepreneur’s name. Marrow Creek road has a daily traffic count of approximately 13,000 cars per day.</p>
    </div>
    <div class="band"></div>
    <div class="photo photo--sign" role="img" aria-label="Photo of the Willowmere Commons pole sign listing tenants beside the stucco retail building"></div>
    <div class="band"></div>
    <div class="photo photo--wide" role="img" aria-label="Wide photo of the shopping center storefronts, parking lot and pole sign"></div>
  </section>

  <section class="page page--back">
    <div class="contact">
      <div class="contact__brand"><span class="contact__square"></span>LARKFIELD REALTY</div>
      <p class="contact__line">1480 Harbor Line Ave, Suite 310</p>
      <p class="contact__line">Fenwick, Texas 75990</p>
      <p class="contact__line">877-555-0142</p>
    </div>
  </section>
</body>
</html>
```